Fernway goods

Organic ethical yoga/activewear that supports kids in need and other community projects by donating % of all sales to these causes. See the product and the brand (Tamrin project) story and catalogue on
Fernwaygoods.com.au
http://files.brisvault.net/doc/q7k2m9_a41c88e0b3d94f27a615c0e2d9b7f443.pdf
Flyer is for fernway goods as the distributor for Tamrin clothing
Would like the flyer to be simple with core message and contact and site details but have a similar feel to the catalogue using some of the art graphics and or photo from site for colour. Also for wholesale/distributor enquiries or to arrange an appointment for a brand presentation contact Marla Quint 0512
Updates
I have four that I am considering so please don't submit any more. One of these will be suitable. Thanks for your submissions.
Marla
Target Market(s)
Yoga studios, wellness centres , private parties, gyms, agents
Industry/Entity Type
Clothing
Look and feel
Each slider illustrates characteristics of the customer's brand and the style your logo design should communicate.

```html
<!DOCTYPE html>
<html lang="en">
<head>
<meta charset="utf-8">
<title>Tamrin project flyer for Fernway goods</title>
<link rel="stylesheet" href="https://fonts.googleapis.com/css2?family=Smokum&family=Delius&family=Alfa+Slab+One&family=Yanone+Kaffeesatz:wght@300;400&display=swap">
<style>
  :root {
    --page-bg: #e9e6e1;
    --mauve: #8c4b6c;
    --mauve-deep: #7a3c5c;
    --mauve-strip: #7f4162;
    --cream: #f2ede3;
    --pattern: #efe9df;
    --pattern-rose: #dcc0cc;
    --pattern-sky: #cfe3e6;
    --mist: #aebbbb;
    --rose-tile: #c47e93;
    --title: #5a1f33;
    --ink: #3e2230;
    --white: #ffffff;
  }
  * { box-sizing: border-box; margin: 0; padding: 0; }
  html, body { width: 1200px; height: 1000px; overflow: hidden; background: var(--page-bg); }
  .flyer { position: absolute; left: 60px; top: 118px; width: 1080px; height: 763px; }
  .flyer-art { position: absolute; inset: 0; width: 1080px; height: 763px; }
  .brand-mark {
    position: absolute; left: 539px; top: 132px; transform: translateX(-50%);
    display: flex; align-items: center; gap: 8px;
    font-family: "Delius", cursive; font-size: 26px; color: var(--white); letter-spacing: 2px;
  }
  .brand-mark .mark-square { width: 16px; height: 16px; background: var(--white); }
  .core-title {
    position: absolute; left: 144px; top: 246px;
    font-family: "Smokum", serif; font-size: 28px; line-height: 32px; color: var(--title); font-weight: 400;
    letter-spacing: 1px;
  }
  .core-body {
    position: absolute; left: 144px; top: 283px;
    font-family: "Delius", cursive; font-size: 14.6px; line-height: 25.3px; color: var(--ink);
    white-space: nowrap;
  }
  .core-body span { display: block; }
  .more-info {
    position: absolute; left: 144px; top: 562px;
    font-family: "Alfa Slab One", serif; font-size: 16px; color: var(--title);
  }
  .trade-contact {
    position: absolute; left: 154px; top: 614px;
    font-family: "Alfa Slab One", serif; font-size: 13.5px; line-height: 18px; color: var(--white);
  }
  .travel-tag {
    position: absolute; left: 766px; top: 196px; width: 180px; transform: translateX(-50%);
    text-align: center; color: var(--white); font-family: "Yanone Kaffeesatz", sans-serif; font-weight: 300;
  }
  .travel-tag .tag-small { display: block; font-size: 24px; line-height: 26px; }
  .travel-tag .tag-large { display: block; font-size: 42px; line-height: 42px; }
  .travel-tag .tag-dots { display: block; font-size: 22px; line-height: 30px; letter-spacing: 4px; }
</style>
</head>
<body>
<main class="flyer">
  <svg class="flyer-art" viewBox="157 176 900 636" xmlns="http://www.w3.org/2000/svg">
    <defs>
      <clipPath id="panel-clip"><rect x="233" y="236" width="767" height="510"/></clipPath>
      <linearGradient id="border-tones" x1="0" y1="0" x2="1" y2="1">
        <stop offset="0" stop-color="var(--pattern-rose)"/>
        <stop offset="0.35" stop-color="var(--pattern)"/>
        <stop offset="0.65" stop-color="var(--pattern-sky)"/>
        <stop offset="1" stop-color="var(--pattern-rose)"/>
      </linearGradient>
    </defs>
    <rect class="outer-frame" x="157" y="176" width="900" height="636" fill="var(--mauve)"/>
    <rect class="frame-inner" x="162" y="181" width="890" height="626" fill="var(--white)"/>
    <g role="img" aria-label="Woven Andean pattern border in mauve, sky blue and grey">
      <rect x="166" y="185" width="882" height="618" fill="url(#border-tones)"/>
    </g>
    <rect class="panel-top" x="233" y="236" width="767" height="144" fill="var(--mauve)"/>
    <rect class="panel-cream" x="233" y="380" width="767" height="292" fill="var(--cream)"/>
    <rect class="panel-bottom" x="233" y="672" width="767" height="68" fill="var(--mauve)"/>
    <polygon class="mist-shape" points="470,380 565,262 790,245 800,672 640,672" fill="var(--mist)" opacity="0.85"/>
    <g role="img" aria-label="Rows of zigzag and triangle ornament">
      <rect x="298" y="262" width="242" height="10" fill="var(--mauve-strip)"/>
      <rect x="308" y="295" width="237" height="31" fill="var(--mauve-strip)"/>
      <rect x="298" y="350" width="242" height="10" fill="var(--mauve-strip)"/>
      <rect x="660" y="262" width="100" height="10" fill="var(--mauve-strip)"/>
      <rect x="660" y="295" width="100" height="31" fill="var(--mauve-strip)"/>
      <rect x="660" y="350" width="100" height="10" fill="var(--mauve-strip)"/>
      <rect x="233" y="731" width="600" height="8" fill="var(--mauve-deep)"/>
    </g>
    <g class="photo-diamonds" clip-path="url(#panel-clip)" stroke="var(--white)" stroke-width="3">
      <polygon role="img" aria-label="Photo of Andean highland hills under cloud" points="880,240 962,322 880,404 798,322" fill="#a7b0a6"/>
      <polygon class="travel-tile" points="795,325 877,407 795,489 713,407" fill="var(--rose-tile)"/>
      <polygon role="img" aria-label="Photo of a pink painted house wall" points="965,325 1047,407 965,489 883,407" fill="#c98aa0"/>
      <polygon role="img" aria-label="Photo of red striped woven textile" points="710,410 792,492 710,574 628,492" fill="#b8404f"/>
      <polygon role="img" aria-label="Photo of a child in a knitted hat" points="880,410 962,492 880,574 798,492" fill="#7c6a52"/>
      <polygon role="img" aria-label="Photo of a girl holding a lamb" points="795,495 877,577 795,659 713,577" fill="#9a918c"/>
      <polygon role="img" aria-label="Photo of a hillside town of brick houses" points="965,495 1047,577 965,659 883,577" fill="#8f96a0"/>
      <polygon role="img" aria-label="Photo of a patterned woven rug" points="880,580 962,662 880,744 798,662" fill="#8e7966"/>
    </g>
  </svg>

  <div class="brand-mark"><span class="mark-square"></span>TAMRIN</div>

  <div class="travel-tag">
    <span class="tag-small">WE</span>
    <span class="tag-large">TRAVEL</span>
    <span class="tag-large">TO EXPLORE</span>
    <span class="tag-dots">•••</span>
  </div>

  <h1 class="core-title">OUR CORE MESSAGE</h1>
  <p class="core-body">
    <span>tamrin Project exists to encourage the creativity&nbsp; of children in</span>
    <span>partnership with select charities in Peru. Their touching drawings</span>
    <span>are turned into graphics used on tamrin products. These</span>
    <span>products are then sold to generate funds for these</span>
    <span>charities to finance projects that allow the children to grow</span>
    <span>up in a crea- tive and safe environment. We are not only dedi-</span>
    <span>cated to providing the children we sponsor with the freedom to</span>
    <span>express themselves, but also strive to provide them with choices and</span>
    <span>opportunities. By nourishing their creative skills,teaching them new artistic</span>
    <span>techniques, and giving value to their work we hope to present art and design</span>
    <span>as a potential path to change their life and future.</span>
  </p>
  <p class="more-info">For More Information visit : www.tamrinproject.com</p>
  <p class="trade-contact">For wholesale/distributor enquiries or to arrange an appointment for a brand<br>presentation contact Marla Quint 0512</p>
</main>
</body>
</html>
```